Velmo Swinger site - new website, blogsite and merchandise point, connection to tradeva

We are a well established Swingers Club in the North east of UK and already have an existing site. www.velmo-example.co.uk, BUT we have changed our logo and our information on the site needs to be updated.

We are changing our hosting site to Nimbrashost.example ,also wanting to start a blog which is linked to the club, plus we wish to sell a small exclusive range of Velmo linked merchandise which will also be available on Tradeva.

I have attached a pdf of the majority of the content. additionally we will provide pictures and a videoclip which should be able to be viewed by pc's, lap tops and mobile phones (the whole website must be fully accessible via phone).

The new site must be able to be updated by someone with medium computer knowledge (usually me), by no means expert. Updates will generally be new pictures and written information. The site must be able to be transferred to NimbrasHost.

Velmo is one of the countries leading clubs and emphasises friendliness, fun & safety for its members, we look after you to ensure your experience is the best we can offer. We are very proud of our reputation, built up over more than 10 years.

Target Market(s)

Swingers, dreamers & fantasists, alternative lifestyle people

Coding

Coded - Design and coding required

Number of Pages Required

5+ page

Font styles to use
Sans Serif

Colors
000000
ec1f27
fbfbfb
eeeeee
eaeaea

Requirements
Must have
• website with blog attached, link to tradeva & quidlo, ability to run videoclip and picture album and must be compatable to transfer easily to Nimbrashost and be updated by non-professional (who can learn)
• Straightforward & easy to navigate
• over 18 content page with enter button
Nice to have
• sexy site
• link to chirpster maybe
• black site would be nice with red or white writing
Should not have
• children and animals in anyway shape or form

```html
<!DOCTYPE html>
<html lang="en">
<head>
<meta charset="utf-8">
<title>Velmo Swingers</title>
<link rel="stylesheet" href="https://fonts.googleapis.com/css2?family=Open+Sans:wght@300;400;600;700&display=swap">
<style>
:root{
  --black:#000000;
  --red:#ec1f27;
  --red-deep:#a8161b;
  --red-bright:#c8090f;
  --white:#fbfbfb;
  --grey-1:#eeeeee;
  --grey-2:#eaeaea;
  --dark:#1d1d1f;
  --text-soft:#d8d8d8;
}
*{margin:0;padding:0;box-sizing:border-box}
html,body{width:1200px;height:3082px;overflow:hidden;background:var(--black)}
body{position:relative;font-family:"Open Sans",Arial,sans-serif;color:var(--white)}
.section{position:absolute;left:0;width:1200px}
.media{position:absolute;display:block}

/* Header / hero */
.hero{top:0;height:623px;background:#1a1210}
.hero-media{left:0;top:0;width:1200px;height:623px;background:radial-gradient(ellipse at 48% 40%,#6a3a28 0%,#3b2218 40%,#170f0c 100%)}
.logo{position:absolute;font-weight:300;letter-spacing:3px;color:var(--white)}
.hero .logo{left:92px;top:44px;font-size:38px}
.nav{position:absolute;top:50px;right:90px;display:flex;gap:8px;list-style:none}
.nav li{font-size:15px;padding:6px 14px;border:2px solid transparent;border-radius:20px;color:var(--white);text-transform:uppercase}
.nav li.active{border-color:var(--white)}
.hero-title{position:absolute;left:0;width:1200px;top:290px;text-align:center;font-size:52px;font-weight:600;letter-spacing:1px}
.hero-sub{position:absolute;left:0;width:1200px;top:350px;text-align:center;font-size:29px;line-height:40px}
.slider-arrows{position:absolute;left:1038px;top:544px;display:flex;gap:8px}
.slider-arrows span{width:26px;height:26px;border-radius:50%;background:rgba(0,0,0,.55);display:flex;align-items:center;justify-content:center}

/* Welcome */
.welcome{top:623px;height:538px;background:linear-gradient(180deg,#1e1e20,#262628)}
.section-title{position:absolute;left:0;width:1200px;text-align:center;font-weight:400;font-size:30px;text-transform:uppercase}
.welcome .section-title{top:72px}
.welcome-text{position:absolute;left:108px;width:984px;top:124px;text-align:center;font-size:14px;line-height:23px;color:var(--text-soft)}
.facility{position:absolute;top:244px;width:234px}
.facility .media{position:relative;width:234px;height:167px}
.facility-label{height:53px;background:var(--white);color:#222;font-size:18px;text-align:center;line-height:53px;text-transform:uppercase}

/* Meet and play */
.meet{top:1161px;height:405px;background:var(--red-deep)}
.meet-title{position:absolute;left:90px;top:88px;font-size:27px;font-weight:400;text-transform:uppercase}
.meet-text{position:absolute;left:90px;top:136px;width:518px;font-size:12px;line-height:23px;text-align:justify}
.pill{position:absolute;background:var(--white);color:#222;border-radius:20px;text-transform:uppercase;text-align:center}
.meet .pill{left:90px;top:306px;width:98px;height:30px;line-height:30px;font-size:11px}
.meet-video{left:670px;top:68px;width:440px;height:263px;background:linear-gradient(135deg,#3a1e3c,#7a2e3a 50%,#c02030)}
.play{position:absolute;left:193px;top:104px}

/* Highlights */
.highlights{top:1566px;height:448px;background:linear-gradient(180deg,#1a1a1c,#252527)}
.highlight{position:absolute;top:109px;width:310px}
.highlight .media{position:relative;width:310px;height:216px}
.highlight-caption{margin-top:16px;text-align:center;font-size:22px}

/* Product */
.product{top:2014px;height:394px;background:linear-gradient(135deg,var(--red-bright),#e0151b 50%,#b8080d)}
.product-media{left:144px;top:51px;width:216px;height:288px;background:linear-gradient(180deg,#fbfbfb,#e2e2e2);border-radius:30px 30px 6px 6px}
.product-title{position:absolute;left:405px;top:100px;font-size:30px;font-weight:400;text-transform:uppercase}
.product-text{position:absolute;left:405px;top:150px;width:680px;font-size:13px;line-height:24px}
.product .pill{left:405px;top:262px;width:135px;height:40px;line-height:40px;font-size:15px}
.store-name{position:absolute;left:559px;top:262px;font-size:28px;line-height:38px;font-weight:700;color:var(--white)}

/* Blog */
.blog{top:2408px;height:387px;background:linear-gradient(180deg,#252527,#1a1a1c)}
.blog .section-title{top:80px}
.post{position:absolute;top:165px;width:500px;height:142px}
.post .media{left:0;top:0;width:163px;height:142px}
.post-body{position:absolute;left:177px;top:0;width:320px}
.post-title{font-size:13px;font-weight:600;color:var(--text-soft)}
.post-date{font-size:13px;margin-top:10px;color:var(--text-soft)}
.post-text{font-size:11px;line-height:19px;margin-top:6px;color:var(--text-soft)}
.post-more{font-size:12px;margin-top:3px;color:var(--text-soft)}

/* Footer */
.footer{top:2795px;height:287px;background:var(--black)}
.footer .logo{left:92px;top:92px;font-size:40px}
.footer-col{position:absolute;top:42px}
.footer-heading{font-size:14px;text-transform:uppercase;margin-bottom:22px}
.footer-col p{font-size:11.5px;line-height:24px}
.signup{display:flex;margin-top:12px}
.signup .field{width:140px;height:32px;background:var(--white);color:#999;font-size:11px;line-height:32px;padding-left:8px}
.signup .submit{width:62px;height:32px;background:var(--red);font-size:12px;text-align:center;line-height:32px}
.social{display:flex;gap:14px}
.social span{width:24px;height:24px;background:var(--white);border-radius:4px}
.footer-rule{position:absolute;left:90px;top:211px;width:1020px;height:1px;background:#444}
.copyright{position:absolute;left:0;width:1200px;top:236px;text-align:center;font-size:12px}
</style>
</head>
<body>

<header class="section hero">
  <div class="media hero-media" role="img" aria-label="Dancer performing on a dimly lit club stage"></div>
  <div class="logo">VELMO</div>
  <ul class="nav">
    <li class="active">Home</li><li>Diary</li><li>Theme Parties</li><li>TV/TG and Admirers</li><li>Membership</li><li>Contact Us</li>
  </ul>
  <h1 class="hero-title">VELMO SWINGERS</h1>
  <p class="hero-sub">Clubs and emphasises friendliness,<br>fun &amp; safety for its members</p>
  <div class="slider-arrows">
    <span><svg width="10" height="12" viewBox="0 0 10 12"><path d="M7 1 2 6l5 5" stroke="#fbfbfb" stroke-width="2" fill="none"/></svg></span>
    <span><svg width="10" height="12" viewBox="0 0 10 12"><path d="M3 1l5 5-5 5" stroke="#fbfbfb" stroke-width="2" fill="none"/></svg></span>
  </div>
</header>

<section class="section welcome">
  <h2 class="section-title">Welcome to Velmo</h2>
  <p class="welcome-text">It is a long established fact that a reader will be distracted by the readable content of a page when looking at its layout. The point of using Lorem Ipsum is that it has a more-or-less normal distribution of letters, as opposed to using 'Content here, content here', making it look like readable English. Many desktop publishing packages and web page editors now use Lorem Ipsum as their default model text</p>
  <div class="facility" style="left:99px"><div class="media" role="img" aria-label="Hot tub room" style="background:linear-gradient(160deg,#c9c49a,#8c8a6c)"></div><div class="facility-label">Hot Tub</div></div>
  <div class="facility" style="left:347px"><div class="media" role="img" aria-label="Sauna lounge with warm lighting" style="background:linear-gradient(160deg,#7a3a22,#2a140e)"></div><div class="facility-label">Sauna</div></div>
  <div class="facility" style="left:595px"><div class="media" role="img" aria-label="Steam room bedroom" style="background:linear-gradient(160deg,#8a6a40,#3a2418)"></div><div class="facility-label">Steam Room</div></div>
  <div class="facility" style="left:843px"><div class="media" role="img" aria-label="Red lit dungeon room" style="background:linear-gradient(160deg,#b23040,#4a1018)"></div><div class="facility-label">Bobs Dungeon</div></div>
</section>

<section class="section meet">
  <h2 class="meet-title">A Great Place to Meet and Play!</h2>
  <p class="meet-text">It is a long established fact that a reader will be distracted by the readable content of a page when looking at its layout. The point of using Lorem Ipsum is that it has a more-or-less normal distribution of letters, as opposed to using 'Content here, content here', making it look like readable English. Many desktop publishing packages and web page editors now use Lorem Ipsum as their default model text, and a search for 'lorem ipsum' will uncover many web sites still in their infancy.</p>
  <div class="pill">Read More</div>
  <div class="media meet-video" role="img" aria-label="Video clip of guests at the club bar">
    <svg class="play" width="54" height="54" viewBox="0 0 54 54"><circle cx="27" cy="27" r="25" fill="rgba(0,0,0,.6)" stroke="#fbfbfb" stroke-width="2"/><path d="M22 17v20l16-10z" fill="#fbfbfb"/></svg>
  </div>
</section>

<section class="section highlights">
  <div class="highlight" style="left:99px"><div class="media" role="img" aria-label="Party guests in evening wear" style="background:linear-gradient(150deg,#6a6a7a,#1e1e28)"></div><p class="highlight-caption">Dress Code</p></div>
  <div class="highlight" style="left:446px"><div class="media" role="img" aria-label="Bar with drinks shelves" style="background:linear-gradient(150deg,#c07a30,#4a2410)"></div><p class="highlight-caption">Alcohol / Drinks</p></div>
  <div class="highlight" style="left:791px"><div class="media" role="img" aria-label="Guests celebrating on the dance floor" style="background:linear-gradient(150deg,#4a6ac0,#2a1440 60%,#8a2a6a)"></div><p class="highlight-caption">TV/TG and Admirers</p></div>
</section>

<section class="section product">
  <div class="media product-media" role="img" aria-label="White Velmo branded t-shirt"></div>
  <h2 class="product-title">Our Product</h2>
  <p class="product-text">Lorem Ipsum has been the industry's standard dummy text ever since the 1500s, when an unknown printer took a galley of type and scrambled it to make a type specimen book. It has survived not only five centuries, but also the leap into electronic typesetting, remaining essentially unchanged</p>
  <div class="pill">Buy Now</div>
  <div class="store-name">tradeva</div>
</section>

<section class="section blog">
  <h2 class="section-title">Latest Blog</h2>
  <article class="post" style="left:90px">
    <div class="media" role="img" aria-label="Club lounge interior" style="background:linear-gradient(150deg,#8a3a2a,#2a1410)"></div>
    <div class="post-body">
      <p class="post-title">Nemo Enim Ipsam Volup</p>
      <p class="post-date">09-07-2017</p>
      <p class="post-text">Lorem Ipsum has been the industry's standard dummy text ever since the 1500s, when an unknown printer took a galley of type and scrambled it to make a type specimen book.</p>
      <p class="post-more">Read More &gt;&gt;</p>
    </div>
  </article>
  <article class="post" style="left:629px">
    <div class="media" role="img" aria-label="Guest bedroom" style="background:linear-gradient(150deg,#b8a888,#4a3a2a)"></div>
    <div class="post-body">
      <p class="post-title">Nemo Enim Ipsam Volup</p>
      <p class="post-date">09-07-2017</p>
      <p class="post-text">Lorem Ipsum has been the industry's standard dummy text ever since the 1500s, when an unknown printer took a galley of type and scrambled it to make a type specimen book.</p>
      <p class="post-more">Read More &gt;&gt;</p>
    </div>
  </article>
</section>

<footer class="section footer">
  <div class="logo">VELMO</div>
  <div class="footer-col" style="left:350px">
    <h3 class="footer-heading">Contact Us</h3>
    <p>Address : 48 Harlow Lane Suite 12<br>Northgate, Tyne 4NE 7QP<br>Phone : 000.555.0142<br>Email : info@velmo-example.co.uk</p>
  </div>
  <div class="footer-col" style="left:637px">
    <h3 class="footer-heading">Join Our Mailing List</h3>
    <p style="line-height:18px;width:200px">Your about us information would fit here nicely.</p>
    <div class="signup"><div class="field">Email address</div><div class="submit">Submit</div></div>
  </div>
  <div class="footer-col" style="left:945px">
    <h3 class="footer-heading">Follow Us Out There</h3>
    <div class="social"><span></span><span></span><span></span><span></span></div>
  </div>
  <div class="footer-rule"></div>
  <p class="copyright">Copyright © 2017 All Rights Reserved</p>
</footer>

</body>
</html>
```